New Business Card Design

We would like to refresh our business cards and make them look better. We are an IT company specialising in Cloud Services, IT Managed Services, software and hardware. I have attached a PSD of our current design. Also attached our logo.
Updates

I have uploaded all new logos in EPS format.

Can you please edit all designs to include a job title for Marcus Hollis, eg. General Manager

Industry/Entity Type

Software

Colors
ffffff

Requirements
Must have
• Please use white background.
Should not have
• Black background

```html
<!DOCTYPE html>
<html lang="en">
<head>
<meta charset="utf-8">
<title>Clearpath Systems – Business Cards</title>
<link href="https://fonts.googleapis.com/css2?family=Questrial&display=swap" rel="stylesheet">
<style>
  :root {
    --backdrop: #e9e7e4;
    --card: #ffffff;
    --ink: #2f3033;
    --grey: #6f767d;
    --red: #a8291d;
    --red-dark: #8c1f16;
  }
  * { box-sizing: border-box; margin: 0; padding: 0; }
  html, body { width: 1200px; height: 900px; overflow: hidden; }
  body {
    background: var(--backdrop);
    font-family: "Questrial", "Century Gothic", sans-serif;
    color: var(--ink);
    position: relative;
  }
  .card {
    position: absolute;
    left: 340px;
    width: 520px;
    height: 296px;
    background: linear-gradient(160deg, #ffffff 0%, #f4f4f4 100%);
    border-radius: 18px;
    box-shadow: 0 10px 28px rgba(0,0,0,0.18);
    overflow: hidden;
  }
  .card--front { top: 110px; }
  .card--back { top: 494px; }

  .brand {
    position: absolute;
    display: flex;
    align-items: center;
    gap: 10px;
    color: var(--grey);
    font-size: 22px;
    letter-spacing: 4px;
    text-transform: lowercase;
    white-space: nowrap;
  }
  .brand__dot {
    width: 22px; height: 22px; border-radius: 50%;
    background: var(--red);
    flex: none;
  }
  .card--front .brand { left: 34px; bottom: 40px; }
  .card--back .brand { right: 30px; top: 36px; font-size: 19px; letter-spacing: 3.5px; }

  .emblem {
    position: absolute;
    border-radius: 50%;
    background: radial-gradient(circle at 40% 35%, var(--red) 0%, var(--red-dark) 100%);
  }
  .card--front .emblem { right: 56px; top: 30px; width: 124px; height: 124px; }
  .card--back .emblem { left: 30px; bottom: 26px; width: 72px; height: 72px; }

  .tagline {
    position: absolute;
    right: 30px;
    top: 176px;
    font-size: 9px;
    letter-spacing: 0.6px;
    color: var(--ink);
    text-transform: uppercase;
  }

  .person { position: absolute; left: 40px; top: 128px; }
  .person__name { font-size: 26px; color: var(--ink); letter-spacing: 0.3px; }
  .person__title { font-size: 10px; color: var(--grey); margin-top: -2px; padding-left: 64px; }

  .contact {
    position: absolute;
    right: 40px;
    top: 150px;
    list-style: none;
    font-size: 12px;
    line-height: 18px;
    color: var(--ink);
  }
  .contact li { display: flex; align-items: center; gap: 10px; }
  .contact svg { width: 9px; height: 9px; fill: var(--grey); flex: none; }
</style>
</head>
<body>
  <section class="card card--front" aria-label="Business card front">
    <div class="emblem" aria-hidden="true"></div>
    <p class="tagline">IT Services, Solutions and Support</p>
    <div class="brand"><span class="brand__dot"></span>clearpath systems</div>
  </section>

  <section class="card card--back" aria-label="Business card back">
    <div class="brand"><span class="brand__dot"></span>clearpath systems</div>
    <div class="person">
      <p class="person__name">Marcus Hollis</p>
      <p class="person__title">general manager</p>
    </div>
    <ul class="contact">
      <li><svg viewBox="0 0 10 10"><path d="M2 0h2l1 3-1.5 1a6 6 0 0 0 2.5 2.5L7 5l3 1v2a2 2 0 0 1-2 2A8 8 0 0 1 0 2a2 2 0 0 1 2-2z"/></svg>07 5550 0142</li>
      <li><svg viewBox="0 0 10 10"><rect x="2" y="0" width="6" height="10" rx="1"/></svg>0400 555 219</li>
      <li><svg viewBox="0 0 10 10"><circle cx="5" cy="5" r="4.5" fill="none" stroke="#6f767d" stroke-width="1.2"/><circle cx="5" cy="5" r="1.6"/></svg>mhollis@clearpathit.com.au</li>
      <li><svg viewBox="0 0 10 10"><path d="M5 0l5 5H8.5v5h-2.5V7H4v3H1.5V5H0z"/></svg>www.clearpathit.com.au</li>
    </ul>
    <div class="emblem" aria-hidden="true"></div>
  </section>
</body>
</html>
```